Home page design for Drone video business (the Business focusses on home videos for realtors)

Dear reader,

*I NEED DESIGNS OF ALL THE PAGES*
We need a first design of a homepage and of 4 other pages of the website of a business that sells drone video services. All the pages will need to be in the similar design style.
The video's are targeted at consumers that want to sell there home and would like to have a cool drone video of photos of their home.

How does the website look:
- has a navbar on top
- A cool looking banner of an areal drone.
- A Big header: with company name: SkyLoftReels
- A smaller subheader: We film your home to increase your chances of sale
- Then a section with a Big header: How does it work
- In this section a place for a vimeo explainitory video
- Then a similar navbar styled bar with a phone number and a email address
- Then a section where the videos porfolio is displayed in a cool way
- Inside this sectiona header: Our work

- A section with header: Why us?
- 4 symbols here with a subheader and some lorum ipsum text underneath (see wireframe images)

- Under that a: Contact us
- where you can put in name, email, phone, message box and a send button

- At the bottom a footer with phone number and a fake address for now.

Be creative. Use creative but serious color.
Use a serious font. Make it a sharp design. Sharp lines. Not to dark design and not to light design.

The wireframes are the same kind of images.
PLEASE PUT IN DESIGNS OF ALL THE PAGES

Good luck

Target Market(s)

People that want to sell home and want to make a cool drone video or photos of their home.

Industry/Entity Type

Business

Contact Information for Business Card

Lucas Wenning
lucas@skyloftreels.example
+31647208351

Logo Text

SkyLoftReels

Number of Pages Required

1 page

Font styles to use
Sans Serif

Requirements
Must have
• All the sections as explained in the instructions.
• The nav bar should have an about us, services, portfolio and a contact us buttons.
• See instruction for details.
• Must include designs of the front page, contact us, our services, portfolio and contact us.
• If you do add some designs for the "about us", "services", "prices", "portfolio" and "contact us" pages, you make a way better chance of winning the competition.
Nice to have
• designs for the other pages as described at the Must haves. You make a better chance of winning if you include them. Look at the wireframes to see the mockups for those pages. think creative about what kind of sections and design should be included in those pages.
Should not have
• bad designs.

```html
<!DOCTYPE html>
<html lang="en">
<head>
<meta charset="utf-8">
<title>SkyLoftReels – Drone videos for home sellers</title>
<link href="https://fonts.googleapis.com/css2?family=Oswald:wght@400;500&family=Roboto:wght@400;500;700&display=swap" rel="stylesheet">
<style>
:root{
  --brand:#2a93d0;
  --bar-left:#3a9fd8;
  --bar-right:#55b6e8;
  --ink:#222;
  --light-bg:#eeeeee;
  --white:#fff;
  --footer:#1b1b1b;
  --field-border:#cfcfcf;
  --player:#1e1e1e;
}
*{box-sizing:border-box;margin:0;padding:0}
html,body{width:1200px;height:2795px;overflow:hidden}
body{font-family:"Roboto",Arial,sans-serif;color:var(--ink);background:var(--white);position:relative}
.abs{position:absolute}
.heading{font-family:"Oswald",Arial,sans-serif;font-weight:500;color:var(--brand);font-size:37px;text-align:center;width:1200px;left:0;letter-spacing:.2px}

/* nav */
.site-nav{top:0;left:0;width:1200px;height:97px;background:var(--white);box-shadow:0 2px 6px rgba(0,0,0,.25);z-index:2}
.brand{left:86px;top:28px;display:flex;align-items:center;gap:14px}
.brand-dot{width:40px;height:40px;border:3px solid var(--brand);border-radius:50%}
.brand-name{font-family:"Oswald",Arial,sans-serif;font-size:27px;color:var(--ink);font-weight:400}
.menu{top:42px;right:90px;display:flex;gap:55px;list-style:none;font-size:16px}
.menu li.active{color:var(--brand)}

/* hero */
.hero{top:97px;left:0;width:1200px;height:559px;overflow:hidden;
  background:
    radial-gradient(ellipse 420px 160px at 260px 440px,rgba(150,90,60,.45),transparent 70%),
    radial-gradient(ellipse 380px 200px at 900px 470px,rgba(120,160,60,.5),transparent 70%),
    radial-gradient(ellipse 500px 140px at 600px 200px,rgba(110,140,70,.55),transparent 70%),
    linear-gradient(180deg,#9db0ad 0%,#7d9a78 10%,#4f7a36 30%,#3d6a28 55%,#4b7a30 80%,#5a853a 100%)}
.hero-title{top:221px;width:1200px;text-align:center;font-family:"Oswald",Arial,sans-serif;font-size:52px;color:var(--white);font-weight:500;text-shadow:0 1px 4px rgba(0,0,0,.35)}
.hero-sub{top:290px;width:1200px;text-align:center;font-size:37px;line-height:41px;color:var(--white);text-shadow:0 1px 4px rgba(0,0,0,.35)}
.dots{top:502px;left:556px;display:flex;gap:9px}
.dots span{width:11px;height:11px;border-radius:50%;background:var(--white)}
.dots span.on{background:var(--brand)}

/* how */
.how{top:656px;left:0;width:1200px;height:574px;background:var(--light-bg)}
.video-frame{left:194px;top:758px;width:812px;height:421px;border:5px solid var(--white);box-shadow:0 0 4px rgba(0,0,0,.25)}
.video-scene{width:100%;height:100%;background:
    radial-gradient(ellipse 160px 90px at 330px 240px,rgba(210,210,190,.55),transparent 70%),
    linear-gradient(180deg,#b9c3c9 0%,#8e9ea0 14%,#4f7a3c 30%,#4a7838 70%,#617f4a 100%)}
.video-actions{right:8px;top:30px;display:flex;flex-direction:column;gap:6px}
.video-actions div{width:50px;height:46px;background:rgba(20,20,20,.75);color:var(--white);font-size:10px;font-weight:500;text-align:center;padding-top:28px}
.player-bar{left:55px;bottom:15px;height:48px;display:flex;align-items:center;gap:14px}
.play{width:90px;height:48px;background:rgba(20,20,20,.85);display:flex;align-items:center;justify-content:center}
.track{width:460px;height:10px;background:rgba(40,40,40,.8);position:relative}
.track i{position:absolute;left:0;top:0;height:10px;width:280px;background:var(--brand)}
.track b{position:absolute;left:252px;top:-24px;background:var(--white);color:var(--ink);font-size:11px;font-weight:500;padding:2px 5px}
.hd{color:var(--brand);font-weight:700;font-size:14px;font-style:normal}

/* contact bar */
.contact-bar{top:1230px;left:0;width:1200px;height:85px;display:flex}
.contact-bar div{width:600px;display:flex;align-items:center;justify-content:center;gap:16px;color:var(--white);font-size:32px}
.contact-bar .phone{background:var(--bar-left)}
.contact-bar .mail{background:var(--bar-right)}

/* work */
.thumb{top:1438px;width:247px;height:250px;border:6px solid var(--white);box-shadow:0 0 5px rgba(0,0,0,.3);display:flex;align-items:center;justify-content:center}
.mini-play{width:62px;height:36px;background:rgba(20,20,20,.75);display:flex;align-items:center;justify-content:center}

/* why */
.why{top:1751px;left:0;width:1200px;height:460px;background:linear-gradient(180deg,#2f96d4,#2287c8)}
.feature{width:470px}
.feature .icon{width:75px;height:70px;background:var(--white);border-radius:4px;display:flex;align-items:center;justify-content:center;box-shadow:0 2px 4px rgba(0,0,0,.2)}
.feature h3{position:absolute;left:84px;top:6px;font-family:"Oswald",Arial,sans-serif;font-weight:400;font-size:21px;color:var(--white)}
.feature p{position:absolute;left:84px;top:40px;width:350px;font-size:12.5px;line-height:19px;color:var(--white);text-align:justify}
.feature .more{position:absolute;left:84px;font-size:11.5px;color:var(--white)}

/* contact */
.contact{top:2211px;left:0;width:1200px;height:421px;background:var(--light-bg)}
.field{background:var(--white);border:1px solid var(--field-border);box-shadow:inset 0 0 0 3px #f6f6f6;font-size:12px;color:#555;padding:16px}
.send{left:453px;top:2552px;width:294px;height:64px;background:linear-gradient(180deg,#5cb3e3,#2a8dcc);color:var(--white);font-size:22px;font-weight:500;display:flex;align-items:center;justify-content:center;border-radius:2px}

/* footer */
.footer-line{top:2632px;left:0;width:1200px;height:10px;background:var(--brand)}
.site-footer{top:2642px;left:0;width:1200px;height:153px;background:var(--footer);color:var(--white)}
.f-phone{left:88px;top:78px;font-size:17px;font-weight:500;display:flex;align-items:center;gap:10px}
.f-addr{left:88px;top:106px;font-size:11.5px}
.f-copy{left:0;width:1200px;text-align:center;top:94px;font-size:11.5px}
.f-brand{right:82px;top:82px;display:flex;align-items:center;gap:12px}
.f-brand .brand-dot{width:34px;height:34px;border-color:var(--white);border-width:2px}
.f-brand .brand-name{color:var(--white);font-size:21px}
</style>
</head>
<body>

<header class="site-nav abs">
  <div class="brand abs"><span class="brand-dot"></span><span class="brand-name">SKYLOFTREELS</span></div>
  <ul class="menu abs">
    <li class="active">HOME</li><li>SERVICES</li><li>ABOUT US</li><li>PORTFOLIO</li><li>CONTACTS</li>
  </ul>
</header>

<section class="hero abs" role="img" aria-label="Aerial photo of farmland with two white camera drones flying">
  <h1 class="hero-title abs">SKYLOFTREELS</h1>
  <p class="hero-sub abs">We film your home to increase<br>your chances of sale</p>
  <div class="dots abs"><span class="on"></span><span></span><span></span><span></span><span></span></div>
</section>

<section class="how abs">
  <h2 class="heading abs" style="top:34px">HOW DOES IT WORK?</h2>
</section>
<div class="video-frame abs">
  <div class="video-scene" role="img" aria-label="Explainer video still: aerial view of a city park with a monument"></div>
  <div class="video-actions abs">
    <div>LIKE</div><div>SHARE</div><div>EMBED</div>
  </div>
  <div class="player-bar abs">
    <div class="play"><svg width="20" height="22" viewBox="0 0 20 22"><path d="M2 1l17 10L2 21z" fill="#fff"/></svg></div>
    <div class="track"><i></i><b>00:34</b></div>
    <i class="hd">HD</i>
    <svg width="14" height="14" viewBox="0 0 14 14" fill="none" stroke="#fff" stroke-width="2"><path d="M1 5V1h4M9 1h4v4M13 9v4H9M5 13H1V9"/></svg>
  </div>
</div>

<div class="contact-bar abs">
  <div class="phone">
    <svg width="30" height="30" viewBox="0 0 30 30"><rect x="1" y="1" width="28" height="28" rx="4" fill="#fff"/><path d="M10 7c1 0 2 3 2 4s-2 1.5-1.5 3c1 2.5 3 4.5 5.5 5.5 1.5.5 2-1.5 3-1.5s4 1 4 2-1.5 3-3.5 3C12 23 7 18 7 10c0-2 2-3 3-3z" fill="var(--bar-left)"/></svg>
    <span>+31647208351</span>
  </div>
  <div class="mail">
    <svg width="34" height="26" viewBox="0 0 34 26"><rect x="1" y="1" width="32" height="24" rx="2" fill="#fff"/><path d="M2 3l15 12L32 3" stroke="var(--bar-right)" stroke-width="3" fill="none"/></svg>
    <span>lucas@skyloftreels.example</span>
  </div>
</div>

<h2 class="heading abs" style="top:1362px">OUR WORK</h2>
<div class="thumb abs" style="left:88px;background:linear-gradient(180deg,#8fb1d8,#b07a4a 60%,#6d8a3e)" role="img" aria-label="Portfolio video: round fisheye view of a town from a drone">
  <div class="mini-play"><svg width="14" height="16" viewBox="0 0 14 16"><path d="M1 1l12 7-12 7z" fill="#fff"/></svg></div></div>
<div class="thumb abs" style="left:348px;background:linear-gradient(180deg,#a8c2d8,#6d8a55 40%,#8b5a3c)" role="img" aria-label="Portfolio video: aerial view of a residential neighbourhood">
  <div class="mini-play"><svg width="14" height="16" viewBox="0 0 14 16"><path d="M1 1l12 7-12 7z" fill="#fff"/></svg></div></div>
<div class="thumb abs" style="left:607px;background:linear-gradient(180deg,#7fb7e6,#4a8fc2 45%,#5f8f3c 75%,#c48a2c)" role="img" aria-label="Portfolio video: hexacopter over a lake with autumn trees">
  <div class="mini-play"><svg width="14" height="16" viewBox="0 0 14 16"><path d="M1 1l12 7-12 7z" fill="#fff"/></svg></div></div>
<div class="thumb abs" style="left:866px;background:linear-gradient(180deg,#4f7a3a,#6d9344 50%,#8a6a4a)" role="img" aria-label="Portfolio video: aerial view of a family house with garden">
  <div class="mini-play"><svg width="14" height="16" viewBox="0 0 14 16"><path d="M1 1l12 7-12 7z" fill="#fff"/></svg></div></div>

<section class="why abs">
  <h2 class="heading abs" style="top:50px;color:#fff">WHY US?</h2>

  <div class="feature abs" style="left:108px;top:140px">
    <div class="icon"><svg width="34" height="30" viewBox="0 0 34 30" fill="none" stroke="var(--brand)" stroke-width="2.5"><path d="M17 2l7 4v8l-7 4-7-4V6z"/><path d="M9 14l7 4v8l-7 4-7-4v-8z"/><path d="M25 14l7 4v8l-7 4-7-4v-8z"/></svg></div>
    <h3>CHEAP</h3>
    <p>Lorem Ipsum has been the industry's standard dummy text ever since the 1500s, when an unknown printer took a galley of type and scrambled it to make</p>
    <span class="more" style="top:98px">Read More »</span>
  </div>

  <div class="feature abs" style="left:650px;top:140px">
    <div class="icon"><svg width="30" height="30" viewBox="0 0 30 30" fill="none" stroke="var(--brand)" stroke-width="3"><circle cx="15" cy="15" r="12"/><circle cx="15" cy="15" r="5"/><path d="M6 6l5 5M24 6l-5 5M6 24l5-5M24 24l-5-5"/></svg></div>
    <h3 style="left:88px">FLEXIBLE</h3>
    <p style="left:88px;top:36px">Lorem Ipsum has been the industry's standard dummy text ever since the 1500s, when an unknown printer took a galley of type and scrambled it to make</p>
    <span class="more" style="left:88px;top:92px">Read More »</span>
  </div>

  <div class="feature abs" style="left:108px;top:284px">
    <div class="icon"><svg width="32" height="28" viewBox="0 0 32 28" fill="none" stroke="var(--brand)" stroke-width="3"><rect x="2" y="2" width="28" height="18"/><path d="M10 26h12M16 20v6"/></svg></div>
    <h3>9K QUALITY</h3>
    <p>Lorem Ipsum has been the industry's standard dummy text ever since the 1500s, when an unknown printer took a galley of type and scrambled it to make</p>
    <span class="more" style="top:98px">Read More »</span>
  </div>

  <div class="feature abs" style="left:650px;top:284px">
    <div class="icon"><svg width="30" height="28" viewBox="0 0 30 28"><path d="M2 13L28 2 22 26 14 18z" fill="var(--brand)"/><path d="M14 18l14-16" stroke="#fff" stroke-width="1.5"/></svg></div>
    <h3 style="left:88px">INCREASE SALE CHANCE</h3>
    <p style="left:88px;top:36px">Lorem Ipsum has been the industry's standard dummy text ever since the 1500s, when an unknown printer took a galley of type and scrambled it to make</p>
    <span class="more" style="left:88px;top:92px">Read More »</span>
  </div>
</section>

<section class="contact abs">
  <h2 class="heading abs" style="top:50px">CONTACT US</h2>
</section>
<div class="field abs" style="left:199px;top:2340px;width:252px;height:54px">Name</div>
<div class="field abs" style="left:473px;top:2340px;width:252px;height:54px">Email id</div>
<div class="field abs" style="left:747px;top:2340px;width:252px;height:54px">Phone</div>
<div class="field abs" style="left:199px;top:2405px;width:802px;height:125px;padding-top:14px">Message</div>
<div class="send abs">SEND</div>

<div class="footer-line abs"></div>
<footer class="site-footer abs">
  <div class="f-phone abs">
    <svg width="16" height="16" viewBox="0 0 30 30"><rect x="1" y="1" width="28" height="28" rx="4" fill="#fff"/><path d="M10 7c1 0 2 3 2 4s-2 1.5-1.5 3c1 2.5 3 4.5 5.5 5.5 1.5.5 2-1.5 3-1.5s4 1 4 2-1.5 3-3.5 3C12 23 7 18 7 10c0-2 2-3 3-3z" fill="#1b1b1b"/></svg>
    +31647208351
  </div>
  <div class="f-addr abs">Address : 1420 Harbor View Rd, Fairhaven, NJ</div>
  <div class="f-copy abs">Copyright © 2016 All Rights</div>
  <div class="f-brand abs"><span class="brand-dot"></span><span class="brand-name">SKYLOFTREELS</span></div>
</footer>

</body>
</html>
```